Wordpress Design Project SEO/SEM Website

Need an updated more professional look for an SEO/SEM existing site.
see: www.brightquill-hub.com

I have an existing logo (in eps format), but am flexible on color and would consider updating the logo if the current colors or design limits your creativity.

Target Market(s)

My customers tend to be marketing managers for mid-size companies with 50+ employees.

Industry/Entity Type

Marketing

Requirements
Must have
• Design should support WordPress 3.0 menus, and widgets.
Nice to have
• Should you want/need it, the font used in the logo is 'ARTLOOKIN'
Should not have
• flash

```html
<!DOCTYPE html>
<html lang="en">
<head>
<meta charset="utf-8">
<title>Brightquill Hub — Internet Marketing</title>
<link rel="stylesheet" href="https://fonts.googleapis.com/css2?family=Arimo:wght@400;700&family=Open+Sans:wght@400&family=Boogaloo&family=Reenie+Beanie&family=Roboto:wght@400&display=swap">
<style>
  :root {
    --page-black: #000000;
    --header-bg: #1a1a1a;
    --hero-bg: #f4efe3;
    --band-1: #1b1b1b;
    --band-2: #282828;
    --band-3: #3a3a3a;
    --sidebar-bg: #434343;
    --footer-bg: #0a0a0a;
    --nav-blue: #1ab0d8;
    --brand-teal: #1f8bb0;
    --connect-blue: #3aa6d9;
    --bubble-rose: #f2435f;
    --bubble-coral: #f9635c;
    --bubble-amber: #f5ae57;
    --text-white: #ffffff;
    --footer-text: #5a5a5a;
  }
  * { box-sizing: border-box; margin: 0; padding: 0; }
  html, body {
    width: 1024px; height: 1200px; overflow: hidden;
    background: var(--page-black);
    font-family: "Arimo", Arial, sans-serif;
    color: var(--text-white);
  }
  .page { position: relative; width: 1024px; height: 1200px; }

  /* Header */
  .site-header { position: absolute; left: 0; top: 0; width: 990px; height: 152px; background: var(--header-bg); }
  .brand { position: absolute; left: 18px; top: 60px; display: flex; align-items: center; gap: 10px; }
  .brand-dot { width: 26px; height: 26px; border-radius: 50%; background: var(--brand-teal); }
  .brand-name { font-family: "Arimo", Arial, sans-serif; font-size: 22px; font-weight: 400; color: var(--brand-teal); letter-spacing: 1px; }
  .header-info { position: absolute; left: 733px; top: 51px; font-size: 12px; font-weight: 700; line-height: 17px; }
  .main-nav { position: absolute; top: 118px; left: 0; width: 990px; font-family: "Open Sans", sans-serif; font-size: 14px; }
  .main-nav a { position: absolute; color: var(--nav-blue); text-decoration: none; white-space: nowrap; }
  .nav-current-rule { position: absolute; left: 375px; top: 111px; width: 67px; height: 1px; background: #3a6f80; }

  /* Hero */
  .hero { position: absolute; left: 0; top: 152px; width: 990px; height: 371px; background: var(--hero-bg); }
  .hero svg { position: absolute; left: 0; top: 0; }
  .bubble-text { position: absolute; top: 137px; width: 220px; }
  .bubble-title { font-family: "Boogaloo", cursive; font-size: 21px; line-height: 24px; margin-bottom: 6px; }
  .bubble-body { font-size: 11px; line-height: 13.5px; }

  /* Content bands */
  .content { position: absolute; left: 0; top: 523px; width: 745px; height: 597px; }
  .feature { position: absolute; left: 0; width: 745px; }
  .feature-internet { top: 0; height: 202px; background: var(--band-1); }
  .feature-quality { top: 202px; height: 220px; background: var(--band-2); }
  .feature-fresh { top: 422px; height: 175px; background: var(--band-3); }
  .feature-art { position: absolute; }
  .feature-title { position: absolute; font-family: "Roboto", Arial, sans-serif; font-size: 22px; font-weight: 400; }
  .feature-body { position: absolute; font-size: 11px; line-height: 13.2px; }
  .feature-body p + p { margin-top: 13px; }

  /* Sidebar */
  .sidebar { position: absolute; left: 745px; top: 523px; width: 245px; height: 597px; background: var(--sidebar-bg); box-shadow: inset 8px 0 8px -4px rgba(0,0,0,0.55); }
  .widget-title { position: absolute; font-family: "Reenie Beanie", cursive; white-space: nowrap; }
  .connect-title { left: 22px; top: 26px; font-size: 32px; color: var(--connect-blue); }
  .social-links { position: absolute; left: 18px; top: 72px; display: flex; gap: 10px; }
  .social-links span { width: 40px; height: 40px; border-radius: 50%; background: linear-gradient(#3f8fd0, #1d5f9e); }
  .posts-title { left: 24px; top: 186px; font-size: 36px; color: var(--text-white); }
  .category-list { position: absolute; left: 24px; top: 226px; list-style: none; font-size: 11px; font-weight: 700; }
  .category-list li { height: 24px; }
  .partner-badge { position: absolute; left: 21px; top: 323px; width: 114px; height: 32px; background: linear-gradient(#f2f2f2, #c8c8c8); }

  /* Footer */
  .site-footer { position: absolute; left: 0; top: 1120px; width: 990px; height: 80px; background: var(--footer-bg); }
  .footer-legal { position: absolute; left: 32px; top: 20px; font-size: 9px; font-weight: 700; line-height: 13px; color: var(--footer-text); }
</style>
</head>
<body>
<div class="page">

  <header class="site-header">
    <div class="brand"><span class="brand-dot"></span><span class="brand-name">Brightquill</span></div>
    <div class="header-info">Brightquill Hub<br>Internet Marketing, Cedarbrook Valley 40210</div>
    <div class="nav-current-rule"></div>
    <nav class="main-nav">
      <a style="left:386px">HOME</a>
      <a style="left:480px">SERVICES</a>
      <a style="left:600px">SEO</a>
      <a style="left:682px">SEM</a>
      <a style="left:767px">ABOUT US</a>
      <a style="left:890px">CONTACT US</a>
    </nav>
  </header>

  <section class="hero">
    <svg width="990" height="371" viewBox="0 0 990 371">
      <g fill="var(--bubble-rose)">
        <ellipse cx="208" cy="165" rx="150" ry="93"/>
        <path d="M325 215 Q340 245 313 276 Q362 252 358 195 Z"/>
      </g>
      <g fill="var(--bubble-coral)">
        <ellipse cx="470" cy="165" rx="152" ry="93"/>
        <path d="M588 215 Q598 245 572 276 Q620 252 618 195 Z"/>
      </g>
      <g fill="var(--bubble-amber)">
        <ellipse cx="748" cy="165" rx="160" ry="93"/>
        <path d="M855 215 Q866 245 842 276 Q895 252 898 195 Z"/>
      </g>
    </svg>
    <div class="bubble-text" style="left:113px">
      <h2 class="bubble-title">Search Engine Optimization</h2>
      <p class="bubble-body">Lorem ipsum dolor site amet, consec tetuer adipic scing elit. Prae sent ves tibulum mo lestie lacus senean nonummy</p>
    </div>
    <div class="bubble-text" style="left:382px">
      <h2 class="bubble-title">Quality Content</h2>
      <p class="bubble-body">Lorem ipsum dolor site amet, consec tetuer adipic scing elit. Prae sent ves tibulum mo lestie lacus senean nonummy</p>
    </div>
    <div class="bubble-text" style="left:652px">
      <h2 class="bubble-title">Site Architecture</h2>
      <p class="bubble-body">Lorem ipsum dolor site amet, consec tetuer adipic scing elit. Prae sent ves tibulum mo lestie lacus senean nonummy</p>
    </div>
  </section>

  <main class="content">
    <article class="feature feature-internet">
      <div class="feature-art" role="img" aria-label="Globe with a gear icon" style="left:36px;top:15px;width:74px;height:74px;border-radius:50%;background:radial-gradient(circle at 35% 35%, #8fd0f5, #1f6fc0 70%, #8a8a8a);"></div>
      <h2 class="feature-title" style="left:161px;top:32px">Internet Marketing</h2>
      <div class="feature-body" style="left:161px;top:83px;width:490px">
        <p>Brightquill Hub provides Search Engine Optimization (SEO) and Search Engine Marketing (SEM) services for the Cedarbrook Valley area. Our focus is optimizing and marketing websites to maximize results.</p>
        <p>Findwell's algorithm employs over 200 variables in determining the ranking of sites. At the core of the algorithm are three elements: Quality Content, Site Architecture, and Incoming Links.</p>
      </div>
    </article>

    <article class="feature feature-quality">
      <div class="feature-art" role="img" aria-label="Documents under a magnifying glass icon" style="left:22px;top:33px;width:113px;height:95px;background:linear-gradient(135deg, #f2d04a, #e8e8e8 45%, #b7c7d6 75%, #c58a2a);"></div>
      <h2 class="feature-title" style="left:152px;top:42px">Quality Content</h2>
      <div class="feature-body" style="left:152px;top:94px;width:500px">
        <p>Your site's content must convey its purpose in a clear fashion and, within seconds, convince your visitors that they have found something worth further exploration. In order for the search engine to target your content, however, the copy must contain key phrases that can be married to the searchers' requests.</p>
      </div>
    </article>

    <article class="feature feature-fresh">
      <div class="feature-art" role="img" aria-label="Circular refresh arrows icon" style="left:25px;top:32px;width:103px;height:92px;border-radius:50%;background:linear-gradient(135deg, #8ccf2e, #1f3a2a 50%, #2a8fd0);"></div>
      <h2 class="feature-title" style="left:152px;top:37px">Freshness</h2>
      <div class="feature-body" style="left:152px;top:89px;width:560px">
        <p>The freshness (or recency) of your content is also a factor in how your content ranks in the search results. This means that businesses that routinely update the content of their website will rank higher in the search results than websites that rarely change.</p>
      </div>
    </article>
  </main>

  <aside class="sidebar">
    <h3 class="widget-title connect-title">connect with us</h3>
    <div class="social-links"><span></span><span></span><span></span></div>
    <h3 class="widget-title posts-title">Posts by Category</h3>
    <ul class="category-list">
      <li>SEM Cedarbrook (44)</li>
      <li>SEO Cedarbrook (46)</li>
      <li>Web Analytics (10)</li>
    </ul>
    <div class="partner-badge"></div>
  </aside>

  <footer class="site-footer">
    <p class="footer-legal">Copyright © 2007-2012 Brightquill Hub, LLC<br>Privacy Policy | &nbsp;Terms and Conditions</p>
  </footer>

</div>
</body>
</html>
```